Construction Company Cellar Crafters needs Business Card

I would like modern looking business card design. I am attaching logo of our company. Please include cell nr 302.418.7650 , email address cellarcrafters4u@examplemail.com, web : cellarcrafters4u.com, please also include wording: Specializing in finishing and remodeling basements. You can play with dark grey and orange colors or any ideas are welcome. Also include social media icons Friendloop and HouseGuidr.

```html
<!DOCTYPE html>
<html lang="en">
<head>
<meta charset="UTF-8">
<title>Cellar Crafters – Business Card</title>
<link rel="stylesheet" href="https://fonts.googleapis.com/css2?family=Source+Sans+3:wght@400;600&display=swap">
<style>
  :root {
    --backdrop-top: #2b2b2b;
    --backdrop-bottom: #060606;
    --card-front: #f3f3f3;
    --brand-orange: #f05a28;
    --ink-dark: #1c1c1c;
    --ink-light: #ffffff;
  }
  * { margin: 0; padding: 0; box-sizing: border-box; }
  html, body {
    width: 1200px;
    height: 900px;
    overflow: hidden;
  }
  body {
    position: relative;
    background: linear-gradient(180deg, var(--backdrop-top) 0%, var(--backdrop-bottom) 100%);
    font-family: "Source Sans 3", "Myriad Pro", sans-serif;
  }
  .card {
    position: absolute;
    top: 184px;
    height: 490px;
    border-radius: 12px;
    text-align: center;
  }
  .card-front {
    left: 299px;
    width: 301px;
    background: var(--card-front);
    color: var(--ink-dark);
  }
  .card-back {
    left: 645px;
    width: 305px;
    background: var(--brand-orange);
    color: var(--ink-light);
  }
  .brand-name {
    position: absolute;
    left: 0;
    right: 0;
    font-weight: 600;
    text-transform: uppercase;
    letter-spacing: 1px;
    line-height: 1;
  }
  .card-front .brand-name {
    top: 150px;
    font-size: 29px;
    color: var(--brand-orange);
  }
  .card-back .brand-name {
    top: 70px;
    font-size: 30px;
    color: var(--ink-light);
  }
  .person {
    position: absolute;
    top: 274px;
    left: 0;
    right: 0;
  }
  .person-name {
    font-size: 16.5px;
    font-weight: 600;
    color: var(--brand-orange);
    line-height: 18px;
  }
  .person-title {
    font-size: 13.5px;
    line-height: 17px;
  }
  .contact {
    position: absolute;
    top: 334px;
    left: 0;
    right: 0;
    list-style: none;
    font-size: 13.5px;
    line-height: 18px;
  }
  .tagline {
    position: absolute;
    top: 198px;
    left: 0;
    right: 0;
    font-size: 25px;
    line-height: 32.5px;
    text-transform: uppercase;
    letter-spacing: 0.8px;
    font-weight: 400;
  }
  .social {
    position: absolute;
    top: 406px;
    left: 0;
    right: 0;
    display: flex;
    justify-content: center;
    gap: 18px;
    list-style: none;
    font-size: 14px;
    font-weight: 600;
  }
  .social-item {
    display: flex;
    align-items: center;
    gap: 6px;
  }
  .social-mark {
    width: 12px;
    height: 12px;
    background: var(--ink-light);
    border-radius: 2px;
  }
</style>
</head>
<body>
  <section class="card card-front" aria-label="Business card front">
    <p class="brand-name">Cellar Crafters</p>
    <div class="person">
      <p class="person-name">Daniel Reyes</p>
      <p class="person-title">Managing Director</p>
    </div>
    <ul class="contact">
      <li>302.418.7650</li>
      <li>cellarcrafters4u@examplemail.com</li>
      <li>cellarcrafters4u.com</li>
    </ul>
  </section>

  <section class="card card-back" aria-label="Business card back">
    <p class="brand-name">Cellar Crafters</p>
    <h2 class="tagline">Specializing<br>in finishing<br>and<br>remodeling<br>basements.</h2>
    <ul class="social">
      <li class="social-item"><span class="social-mark"></span>Friendloop</li>
      <li class="social-item"><span class="social-mark"></span>HouseGuidr</li>
    </ul>
  </section>
</body>
</html>
```